Website for "Bright Morrow Ltd" cleaning bsuiness

We require a website to expose our business to the local market. We want to provide background on who we are and what we do but in an easily digestible way. We clean domestic and commercial premises and want to provide a list of all of our services to potential customers. We operate out of Warrington in the UK.

We would like the website to be animated in some way so that the experience of using it is not dull or mundane. This website needs to be an extension of our company.

Target Market(s)

30 - 60 year olds for Domestic plus commercial clients

Industry/Entity Type

Cleaning Service

Coding

Coded - Design and coding required

Number of Pages Required

4 page

Font styles to use
Sans Serif

Colors
0455a3
3176b5
85acd3
cfdeed
ffffff
000000
1b1b1b
c8c8c8
757575

Requirements
Must have
• Logo which has been provided. Theme based around the logo and its colours. Simple layout to avoid confusion.
Nice to have
• Animations where possible to impress the customer.
Should not have
• any pictures of cleaning equipment, fairies, maids etc

```html
<!DOCTYPE html>
<html lang="en">
<head>
<meta charset="utf-8">
<title>Bright Morrow Ltd – Professional Cleaning Service</title>
<link href="https://fonts.googleapis.com/css2?family=Roboto:wght@400;500;700&family=Jost:wght@400;500&family=Lobster+Two:ital,wght@1,700&display=swap" rel="stylesheet">
<style>
:root{
  --blue:#0455a3;
  --blue-mid:#3176b5;
  --blue-soft:#85acd3;
  --blue-pale:#cfdeed;
  --bright:#1683ee;
  --white:#ffffff;
  --black:#000000;
  --ink:#1b1b1b;
  --grey:#c8c8c8;
  --grey-dark:#757575;
  --mist:#efefef;
}
*{margin:0;padding:0;box-sizing:border-box}
html,body{width:1200px;height:2853px;overflow:hidden}
body{position:relative;background:var(--white);font-family:'Roboto',sans-serif;color:var(--ink)}
.abs{position:absolute}
svg.shape{position:absolute;left:0;display:block}

/* header */
.top-line{left:0;top:0;width:1200px;height:4px;background:var(--blue)}
.nav a{position:absolute;top:50px;font:500 16px 'Roboto',sans-serif;color:var(--ink);text-decoration:none;transform:translateX(-50%);letter-spacing:.3px}
.nav a.active{color:var(--blue)}
.nav a.active::after{content:"";position:absolute;left:-4px;right:-4px;bottom:-8px;height:3px;background:var(--blue)}
.brand{left:600px;top:26px;transform:translateX(-50%);display:flex;align-items:center;gap:10px;white-space:nowrap}
.brand .dot{width:18px;height:18px;border-radius:50%;background:var(--blue)}
.brand span{font:500 26px 'Jost',sans-serif;color:var(--blue)}

/* hero */
.hero-photo{left:0;top:95px;width:1200px;height:500px;background:linear-gradient(180deg,#6b7f99 0%,#3d4652 35%,#262b31 70%,#4d4a44 100%)}
.hero-title{left:232px;top:280px;width:738px;height:68px;background:rgba(4,85,163,.85);color:var(--white);font:400 42px 'Jost',sans-serif;text-align:center;line-height:68px;letter-spacing:.5px}
.hero-sub{left:0;width:1200px;top:364px;text-align:center;color:var(--white);font:italic 700 34px 'Lobster Two',cursive}
.hero-btn{left:538px;top:456px;width:126px;height:46px;border:2px solid var(--white);color:var(--white);font:500 17px 'Roboto',sans-serif;line-height:42px;text-align:center;background:rgba(0,0,0,.25)}

/* info band */
.info-band{left:0;top:595px;width:1200px;height:110px;background:var(--bright)}
.info{position:absolute;top:632px;color:var(--white)}
.info p{font-size:18px;line-height:34px}
.info strong{font-weight:500}
.info svg{position:absolute;left:-40px;top:6px}

/* section headings */
.eyebrow{left:0;width:1200px;text-align:center;font:400 22px 'Jost',sans-serif}
.heading{left:0;width:1200px;text-align:center;font:400 32px 'Jost',sans-serif}
.intro{left:160px;width:880px;top:888px;text-align:center;font-size:13.5px;line-height:26px;color:var(--grey-dark)}

/* service cards */
.card{position:absolute;top:974px;width:209px;height:399px;border-radius:105px 105px 0 0;color:var(--white);text-align:center;box-shadow:0 14px 14px -10px rgba(0,0,0,.35)}
.card .pic{position:absolute;left:4px;top:4px;width:201px;height:201px;border-radius:50%}
.card h3{position:absolute;top:228px;width:100%;font:500 20px 'Jost',sans-serif}
.card p{position:absolute;top:270px;left:14px;right:14px;font-size:12.5px;line-height:24px}
.card .more{position:absolute;top:358px;width:100%;font:700 14px 'Roboto',sans-serif}
.card-blue{background:var(--blue)}
.card-dark{background:#333333}
.card-mid{background:var(--blue-mid)}
.card-black{background:var(--ink)}

/* who we are */
.who-bg{left:0;top:1400px;width:1200px;height:705px}
.feature{position:absolute;top:1626px;width:240px;text-align:center;color:var(--white);transform:translateX(-50%)}
.feature .ring{width:114px;height:114px;margin:0 auto;border-radius:50%;border:2px solid var(--white);display:flex;align-items:center;justify-content:center}
.feature .ring.on{background:var(--blue-pale);border-color:var(--blue-pale)}
.feature h4{margin-top:20px;font:500 17px 'Roboto',sans-serif}
.detail-pic{left:99px;top:1832px;width:253px;height:203px;border:3px solid var(--white);background:linear-gradient(180deg,#d8d8d6 0%,#9a9a9a 45%,#3c3c3c 70%,#e4e4e2 100%)}
.detail{left:378px;top:1832px;width:725px;color:var(--white)}
.detail h3{font:500 21px 'Roboto',sans-serif;margin-bottom:10px}
.detail p{font-size:13px;line-height:25px;margin-bottom:8px;color:#e6eef7}

/* testimonials */
.testi-bg{left:0;top:2063px;width:1200px;height:324px;background:var(--mist)}
.quote{left:230px;width:740px;top:2284px;text-align:center;font-size:16px;line-height:31px;color:#333}
.qmark{font:700 70px Georgia,serif;color:var(--blue);line-height:1}
.author{left:0;width:1200px;top:2370px;text-align:center;color:var(--blue);font:500 17px 'Roboto',sans-serif}

/* footer */
.footer-bg{left:0;top:2387px;width:1200px;height:405px}
.foot-brand{left:99px;top:2600px;display:flex;align-items:center;gap:10px}
.foot-brand .dot{width:18px;height:18px;border-radius:50%;background:var(--white)}
.foot-brand span{font:500 28px 'Jost',sans-serif;color:var(--white);white-space:nowrap}
.foot-col{position:absolute;top:2496px;color:var(--white)}
.foot-col h5{font:700 16px 'Roboto',sans-serif;letter-spacing:.5px;padding-bottom:10px;border-bottom:1px solid rgba(255,255,255,.35);display:inline-block;margin-bottom:18px}
.links li{list-style:none;font-size:14px;line-height:31.8px}
.contact-item{position:relative;padding-left:56px;margin-bottom:12px;font-size:12.5px;line-height:20px}
.contact-item b{font-size:14px;font-weight:700;display:block}
.contact-item .ico{position:absolute;left:0;top:2px;width:36px;height:36px;border-radius:50%;background:var(--white);display:flex;align-items:center;justify-content:center}
.field{position:absolute;border:1px solid rgba(255,255,255,.75);border-radius:3px;color:var(--white);font-size:11px;padding:10px 12px}
.send{position:absolute;left:814px;top:2674px;width:118px;height:38px;background:var(--blue);color:var(--white);font:500 11px 'Roboto',sans-serif;line-height:38px;text-align:center;border-radius:2px}
.bottom-bar{left:0;top:2792px;width:1200px;height:61px;background:var(--blue);color:var(--white)}
.bottom-bar p{position:absolute;left:99px;top:22px;font-size:13px}
.social{position:absolute;top:13px;width:34px;height:34px;border-radius:50%;border:2px solid var(--white)}
</style>
</head>
<body>

<!-- header -->
<div class="abs top-line"></div>
<nav class="nav">
  <a class="active" style="left:122px">HOME</a>
  <a style="left:264px">ABOUT US</a>
  <a style="left:430px">SERVICES</a>
  <a style="left:776px">PORTFOLIO</a>
  <a style="left:919px">BLOG</a>
  <a style="left:1061px">CONTACT</a>
</nav>
<div class="abs brand"><i class="dot"></i><span>Bright Morrow Ltd</span></div>

<!-- hero -->
<div class="abs hero-photo" role="img" aria-label="Photo of a modern glass-fronted office building under a cloudy blue sky"></div>
<svg class="shape" style="top:310px" width="1200" height="60" viewBox="0 0 1200 60">
  <polyline points="44,8 28,30 44,52" fill="none" stroke="#fff" stroke-width="2.5"/>
  <polyline points="1136,8 1152,30 1136,52" fill="none" stroke="#fff" stroke-width="2.5"/>
</svg>
<h1 class="abs hero-title">WELCOME TO BRIGHT MORROW</h1>
<p class="abs hero-sub">We clean domestic and commercial premises</p>
<div class="abs hero-btn">Read More</div>

<!-- info band -->
<div class="abs info-band"></div>
<svg class="shape" style="top:704px" width="1200" height="44" viewBox="0 0 1200 44"><polygon points="0,0 1200,0 1200,1 600,42 0,1" fill="#1683ee"/></svg>
<div class="info" style="left:156px">
  <svg width="30" height="30" viewBox="0 0 24 24" fill="none" stroke="#fff" stroke-width="1.5"><path d="M5 3h4l2 5-2.5 1.5a11 11 0 0 0 6 6L16 13l5 2v4a2 2 0 0 1-2 2A17 17 0 0 1 3 5a2 2 0 0 1 2-2z"/></svg>
  <p>Have a question? Call us now</p><p><strong>+1800 4417 2290</strong></p>
</div>
<div class="info" style="left:512px">
  <svg width="30" height="30" viewBox="0 0 24 24" fill="none" stroke="#fff" stroke-width="1.5"><circle cx="12" cy="12" r="10"/><path d="M12 6v6l4 2"/></svg>
  <p>We are open Mon-Fri</p><p><strong>Mon – Fri 08:00 – 17:00</strong></p>
</div>
<div class="info" style="left:835px">
  <svg width="32" height="30" viewBox="0 0 24 24" fill="none" stroke="#fff" stroke-width="1.5"><rect x="2" y="5" width="20" height="14"/><path d="M2 5l10 8 10-8"/></svg>
  <p>Need support? Drop us an email</p><p><strong>support@brightmorrow.co.uk</strong></p>
</div>

<!-- what we do -->
<p class="abs eyebrow" style="top:796px;color:var(--ink)">What We Do</p>
<h2 class="abs heading" style="top:834px;color:var(--blue)">Professional Cleaning Service Company</h2>
<p class="abs intro">Our friendly team keeps homes and workplaces across Warrington spotless, using careful methods and trusted products. We tailor every visit to your space, your schedule and your standards, so you can relax and enjoy a cleaner, brighter place to live and work.</p>

<div class="card card-blue" style="left:124px">
  <div class="pic" role="img" aria-label="Photo of a bright open-plan dining room" style="background:linear-gradient(160deg,#f3efe8,#c9b79f 55%,#b8452c)"></div>
  <h3>Cleaning Services</h3>
  <p>We clean domestic and commercial premises and want to provide a list of all.</p>
  <div class="more">Read More ➜</div>
</div>
<div class="card card-dark" style="left:373px">
  <div class="pic" role="img" aria-label="Photo of a café interior with chairs and tables" style="background:linear-gradient(160deg,#5a4a3c,#a48c70 55%,#e2d6c4)"></div>
  <h3>Commercial Premises</h3>
  <p>We clean domestic and commercial premises and want to provide a list of all.</p>
  <div class="more">Read More ➜</div>
</div>
<div class="card card-mid" style="left:622px">
  <div class="pic" role="img" aria-label="Photo of a white modern kitchen and dining area" style="background:linear-gradient(160deg,#ffffff,#dfe3e6 55%,#a58f78)"></div>
  <h3>Domestic Premises</h3>
  <p>We clean domestic and commercial premises and want to provide a list of all.</p>
  <div class="more">Read More ➜</div>
</div>
<div class="card card-black" style="left:869px">
  <div class="pic" role="img" aria-label="Photo of townhouses with a green lawn and palm tree" style="background:linear-gradient(180deg,#d6e6f3 0%,#eae6dc 45%,#6fa33b 70%,#3f7a22 100%)"></div>
  <h3>Potential Customers</h3>
  <p>We clean domestic and commercial premises and want to provide a list of all.</p>
  <div class="more">Read More ➜</div>
</div>

<!-- who we are -->
<svg class="shape who-bg" width="1200" height="705" viewBox="0 0 1200 705" role="img" aria-label="Faint photo of an office building behind a blue overlay">
  <defs><linearGradient id="whoGrad" x1="0" y1="0" x2="1" y2="1"><stop offset="0" stop-color="#0a5fb0"/><stop offset=".6" stop-color="#0455a3"/><stop offset="1" stop-color="#1d5f9c"/></linearGradient></defs>
  <polygon points="0,0 600,48 1200,0 1200,663 600,705 0,663" fill="url(#whoGrad)"/>
</svg>
<svg class="shape" style="top:2063px" width="1200" height="44" viewBox="0 0 1200 44"><polygon points="0,0 1200,0 600,42" fill="#0455a3"/></svg>
<p class="abs eyebrow" style="top:1507px;color:var(--white)">Who We Are</p>
<h2 class="abs heading" style="top:1545px;color:var(--white)">Superior Cleaning Solutions</h2>

<div class="feature" style="left:196px">
  <div class="ring on"><svg width="52" height="52" viewBox="0 0 24 24" fill="none" stroke="#0455a3" stroke-width="1.3"><path d="M3 11l9-8 9 8"/><path d="M5 10v10h14V10"/><path d="M10 20v-6h4v6"/></svg></div>
  <h4>Home Maintenance</h4>
</div>
<div class="feature" style="left:453px">
  <div class="ring"><svg width="56" height="52" viewBox="0 0 26 24" fill="#fff"><rect x="3" y="9" width="4" height="12"/><rect x="8" y="5" width="5" height="16"/><rect x="14" y="7" width="5" height="14"/><rect x="20" y="11" width="3" height="10"/></svg></div>
  <h4>Commercial Maintenance</h4>
</div>
<div class="feature" style="left:719px">
  <div class="ring"><svg width="50" height="52" viewBox="0 0 24 24" fill="none" stroke="#fff" stroke-width="1.4"><rect x="5" y="3" width="14" height="18"/><path d="M8 7h2M14 7h2M8 11h2M14 11h2M8 15h2M14 15h2M11 21v-3h2v3"/></svg></div>
  <h4>Domestic Maintenance</h4>
</div>
<div class="feature" style="left:976px">
  <div class="ring"><svg width="50" height="50" viewBox="0 0 24 24" fill="#fff"><path d="M12 2l1.8 6.2L20 10l-6.2 1.8L12 18l-1.8-6.2L4 10l6.2-1.8z"/><circle cx="19" cy="18" r="2"/><circle cx="5" cy="19" r="1.4"/></svg></div>
  <h4>Cleaning Services</h4>
</div>

<div class="abs detail-pic" role="img" aria-label="Photo of a modern living room with a grey sofa and wall-mounted television"></div>
<div class="abs detail">
  <h3>Home Maintenance</h3>
  <p>From weekly tidies to deep seasonal cleans, we look after every room in your home with the same care we would give our own. Kitchens, bathrooms, bedrooms and living spaces are dusted, polished and refreshed, and we always leave floors gleaming. Our staff are vetted, insured and fully trained, so you can trust us with your keys.</p>
  <p>Book a single visit or set up a regular plan that suits your week. We bring our own supplies, work quietly around your routine and check every job before we leave, so your home feels fresh, calm and ready to enjoy.</p>
</div>

<!-- testimonials -->
<div class="abs testi-bg"></div>
<svg class="shape" style="top:2063px" width="1200" height="44" viewBox="0 0 1200 44"><polygon points="0,0 1200,0 600,42" fill="#0455a3"/></svg>
<h2 class="abs heading" style="top:2186px;color:var(--blue);font-size:30px">Client Testimonials</h2>
<div class="abs qmark" style="left:180px;top:2258px">“</div>
<div class="abs qmark" style="left:982px;top:2320px">”</div>
<p class="abs quote">Sed ut perspiciatis unde omnis iste natus error sit voluptatem accusantium doloremque laudantium, totam rem aperiam, eaque ipsa quae ab illo inventore veritatis et quasi architecto</p>
<p class="abs author">- Helen Parker</p>

<!-- footer -->
<svg class="shape footer-bg" width="1200" height="405" viewBox="0 0 1200 405" role="img" aria-label="Dark photo of an office building at dusk">
  <defs><linearGradient id="footGrad" x1="0" y1="0" x2="1" y2="1"><stop offset="0" stop-color="#1c2736"/><stop offset=".5" stop-color="#0c1622"/><stop offset="1" stop-color="#18202b"/></linearGradient></defs>
  <rect width="1200" height="405" fill="url(#footGrad)"/>
  <polygon points="0,0 1200,0 600,58" fill="#efefef"/>
</svg>
<div class="abs foot-brand"><i class="dot"></i><span>Bright Morrow Ltd</span></div>

<div class="foot-col" style="left:401px">
  <h5>QUICK LINKS</h5>
  <ul class="links">
    <li>› Home</li><li>› About Us</li><li>› Services</li><li>› Portfolio</li><li>› Blog</li><li>› Contact Us</li>
  </ul>
</div>
<div class="foot-col" style="left:578px;width:210px">
  <h5>CONTACT US</h5>
  <div class="contact-item">
    <span class="ico"><svg width="16" height="18" viewBox="0 0 24 24" fill="#1b1b1b"><path d="M12 2a7 7 0 0 0-7 7c0 5 7 13 7 13s7-8 7-13a7 7 0 0 0-7-7zm0 9.5A2.5 2.5 0 1 1 12 6.5a2.5 2.5 0 0 1 0 5z"/></svg></span>
    <b>BRIGHT MORROW,</b>Kingfisher Court<br>48 Lindale Road, UK
  </div>
  <div class="contact-item">
    <span class="ico"><svg width="12" height="18" viewBox="0 0 14 24" fill="none" stroke="#1b1b1b" stroke-width="2"><rect x="2" y="2" width="10" height="20" rx="2"/></svg></span>
    <b>PHONE:</b>1800 4417 2290
  </div>
  <div class="contact-item">
    <span class="ico"><svg width="16" height="14" viewBox="0 0 24 20" fill="#1b1b1b"><path d="M2 2h20v2l-10 7L2 4z"/><path d="M2 7l10 7 10-7v11H2z"/></svg></span>
    <b>Mail:</b>info@brightmorrow.co.uk
  </div>
</div>
<div class="foot-col" style="left:814px">
  <h5>CONTACT FORM</h5>
</div>
<div class="field" style="left:814px;top:2551px;width:137px;height:36px">Name</div>
<div class="field" style="left:961px;top:2551px;width:138px;height:36px">Phone</div>
<div class="field" style="left:814px;top:2594px;width:285px;height:65px">Message</div>
<div class="send">SEND MESSAGE</div>

<div class="abs bottom-bar">
  <p>Copyright © 2016 Bright Morrow. All Right Reserved</p>
  <span class="social" style="left:949px"></span>
  <span class="social" style="left:991px"></span>
  <span class="social" style="left:1033px"></span>
  <span class="social" style="left:1067px"></span>
</div>

</body>
</html>
```